Web design for Crowdfunding site HopeWingsRally.com

We need a web design for christian crowdfunding website. Here is the challenge: We need responsive layout that is targeted first in iPad size of screen. It should also scale somehow down to iPhone size of screens. Web layout can be about the same size as iPad screen.

Screens should work so that main page scrolls not but only certain part of the screen scrolls and always one "page" at time. We can implement these "scrolls" then later with javascript but now we need only design. The challenge is to create this kind of hybrid website / app look.

Target is at first to raise funds to orphan people needing about $40 per month for their living and education. There is always some organization which takes care of these kids. Later there will be other christian missions included. At first we are looking to find monthly supporters.

You can be as creative as you want :) As you see from the look and feel sector, I am not looking any same traditional look which many "help kids" sites have. I am looking to reach now younger generation and therefore iPad and mobile are the main screen sizes.

Inspirational designs:
- https://example-gallery.test/profiles/studiofernlake/designs/482716?from=%2Fbrowse%2Fxhr%2Fdesigns%3Fcategory%3Dmobile-app-design
- http://www.artpoolhub.test/design/8261047 Clear, simple visuals
- http://www.artpoolhub.test/design/7394215 Header
- http://www.artpoolhub.test/design/6048392 Contrast in the colors, i think is powerfull

Some terms could be: Kids play, kids are learning (in the school). No static posture but living like kids are. I wonder also how we could also add little bit gaming style even though the question is of reali life of real people. Giving should be rewarding.

Target Market(s)

People who want help other people.

Industry/Entity Type

Christian

Number of Pages Required

4 page

Requirements
Must have
• Homepage. Mission page (In my wireframes it was one kid).
Nice to have
• Other pages and some idea how to scroll. 4 pages is no must. If you feel easy, please give first some draft and I give comments on that.

```html
<!DOCTYPE html>
<html lang="en">
<head>
<meta charset="utf-8">
<title>HopeWingsRally — Mission Maria</title>
<link rel="stylesheet" href="https://fonts.googleapis.com/css2?family=Lato:wght@400;700;900&family=Roboto:wght@400;500;700&family=Tinos:wght@400;700&display=swap">
<style>
:root{
  --green:#2cc46b;
  --green-dark:#23a95a;
  --teal:#1f9e8e;
  --ink:#1d1d1f;
  --text:#333338;
  --muted:#7b7b85;
  --line:#b9b9c6;
  --about-bg:#dcdbe8;
  --activity-bg:#eeeef3;
  --team-bg:#cfcedd;
  --card:#ffffff;
  --footer:#3b3b3d;
  --accent-red:#e8242c;
  --dot-blue:#2d7fe6;
  --orange:#f07a1c;
  --avatar:#c9c9cf;
}
*{box-sizing:border-box;margin:0;padding:0}
html,body{width:1200px;height:3000px;overflow:hidden}
body{font-family:"Roboto",Arial,sans-serif;color:var(--text);background:#fff;position:relative}
.abs{position:absolute}

/* header */
.site-header{position:absolute;left:0;top:0;width:1200px;height:65px;background:var(--green);color:#fff;font-family:"Lato",Arial,sans-serif}
.menu-toggle{position:absolute;left:18px;top:17px;display:flex;align-items:center;gap:14px;font-weight:700;font-size:19px;letter-spacing:.2px}
.menu-toggle svg{display:block}
.brand{position:absolute;left:0;right:0;top:7px;text-align:center;font-weight:900;font-size:46px;letter-spacing:1px;color:#fff}
.account-links{position:absolute;right:22px;top:21px;display:flex;gap:22px;font-weight:700;font-size:19px}

/* hero */
.hero{position:absolute;left:0;top:65px;width:1200px;height:745px;background:radial-gradient(ellipse at 50% 55%,#c9c9c9 0%,#9a9a9a 45%,#5d5d5d 80%,#dedede 100%)}
.hero-quote{position:absolute;left:0;right:0;top:12px;text-align:center;font-family:"Lato",Arial,sans-serif;font-weight:700;font-size:14px;line-height:19px;color:var(--green)}
.hero-quote .lead{color:var(--ink);font-size:17px;line-height:22px}
.hero-quote .amount{color:var(--accent-red);font-weight:900}
.hero-band{position:absolute;left:0;top:810px;width:1200px;height:40px;background:var(--green)}

/* sections */
.section{position:absolute;left:0;width:1200px}
.about{top:850px;height:678px;background:var(--about-bg)}
.activities{top:1528px;height:707px;background:var(--activity-bg)}
.team{top:2235px;height:675px;background:var(--team-bg)}
.section-title{position:absolute;left:0;right:0;text-align:center;font-family:"Tinos","Times New Roman",serif;font-weight:700;font-size:46px;color:#000;letter-spacing:1px}
.section-title.soft{font-weight:400;color:#8a8a92}

/* mission story */
.mission-title{position:absolute;font-family:"Roboto",Arial,sans-serif;font-size:26px;font-weight:500;color:#222}
.tabs{position:absolute;display:flex;height:27px;background:#c4c4cc;font-size:12px;color:#333}
.tabs span{flex:1;display:flex;align-items:center;justify-content:center}
.tabs .active{background:#ececf1}
.story p{font-size:14.2px;line-height:15.2px;color:#222;margin-bottom:15px}
.timeline{position:absolute;left:162px;top:190px;width:14px;height:440px}
.timeline .rail{position:absolute;left:5px;top:8px;width:5px;height:424px;background:#a3a3ab}
.timeline .knob{position:absolute;left:0;width:15px;height:15px;border-radius:50%;background:#a3a3ab}
.timeline .now{left:-3px;width:21px;height:21px;background:var(--orange)}
.story-still{position:relative;width:335px;height:126px;margin:-2px 0 18px 68px;background:linear-gradient(90deg,#1a1a1a 0%,#3a3a3a 55%,#8d8d8d 75%,#2a2a2a 100%)}
.story-still .caption{position:absolute;left:70px;top:42px;width:150px;text-align:right;font-size:9px;line-height:12px;color:#fff}
.story-still .caption em{font-style:normal;color:#f3c23a}

/* funding panel */
.fund-panel{position:absolute;width:305px;font-family:"Roboto",Arial,sans-serif}
.fund-panel h3{font-size:26px;font-weight:500;color:#222;margin-bottom:10px}
.fund-panel .place{display:flex;align-items:center;gap:8px;font-size:14px;color:#333;margin-left:3px}
.fund-panel .org{font-size:14px;margin:10px 0 0 3px}
.support-row{display:flex;align-items:center;margin-top:16px;padding-bottom:6px;border-bottom:2px solid var(--line);font-size:14px}
.support-row .label{flex:1}
.mini-avatar{width:22px;height:22px;border-radius:50%;background:var(--avatar);border:2px solid #8f8f97;margin-left:9px;position:relative;overflow:hidden}
.mini-avatar::after{content:"";position:absolute;left:4px;top:10px;width:10px;height:10px;border-radius:50%;background:#8f8f97}
.my-support{display:flex;align-items:center;justify-content:space-between;font-weight:700;font-size:14px;margin-top:12px;padding-right:52px}
.close-dot{width:18px;height:18px;border-radius:50%;background:#fff;color:#aaa;font-size:13px;display:flex;align-items:center;justify-content:center;font-weight:400}
.fund-stats{display:flex;align-items:center;gap:20px;margin-top:4px;border-bottom:2px solid var(--line);padding-bottom:8px}
.fund-stats .given{font-weight:700;font-size:15px}
.fund-stats small{display:block;font-size:12px;margin:5px 0 8px}
.fund-stats .need{display:flex;align-items:center;gap:8px;font-size:14px;font-weight:500}
.participate{font-size:14px;margin-top:12px;padding-bottom:6px;border-bottom:2px solid var(--line)}
.options{list-style:none;margin-top:8px}
.options li{height:40px;background:#fff;margin-bottom:7px;display:flex;align-items:center;padding:0 10px;font-size:14px;font-weight:500;color:#222;box-shadow:0 1px 2px rgba(0,0,0,.12)}
.options .swatch{width:24px;height:24px;background:var(--teal);margin-right:14px;border-radius:2px}
.options .label{flex:1}
.options .amount-field{width:130px;height:30px;border:1px dashed #bbb;display:flex;align-items:center;padding-left:14px;font-size:12px;font-weight:400;margin-right:12px}

/* profile */
.profile-photo{position:absolute;left:182px;top:87px;width:143px;height:143px;border-radius:50%;background:#d3d3d8;border:4px solid #8e8e96;overflow:hidden}
.profile-photo::before{content:"";position:absolute;left:38px;top:22px;width:60px;height:70px;border-radius:50%;background:#a9a9b0}
.profile-photo::after{content:"";position:absolute;left:10px;top:92px;width:116px;height:80px;border-radius:50% 50% 0 0;background:#a9a9b0}
.profile-meta{position:absolute;left:373px;top:108px;font-size:14px;line-height:32px;color:#222}
.following{position:absolute;left:750px;top:108px;font-size:14px;color:#222}
.following h4{font-size:13px;font-weight:500;margin-bottom:12px}
.following li{list-style:none;display:flex;align-items:center;gap:12px;height:35px;font-size:14px}
.following .mini-avatar{margin-left:0}
.list-head{position:absolute;font-size:14px;color:#333;display:flex;align-items:center;gap:10px;letter-spacing:.3px}

.mission-card{position:absolute;width:416px;height:80px;background:#fff;display:flex;align-items:center;padding:0 12px;font-size:14px}
.mission-card .avatar{width:58px;height:58px;border-radius:50%;background:#e3e3e7;border:2px solid #9a9aa2;position:relative;overflow:hidden;margin-right:14px}
.mission-card .avatar::after{content:"";position:absolute;left:13px;top:10px;width:28px;height:28px;border-radius:50%;background:#b2b2b8;box-shadow:0 30px 0 8px #b2b2b8}
.mission-card .who{flex:1;line-height:18px;color:#222}
.mission-card .dot{width:11px;height:11px;border-radius:50%;background:var(--dot-blue);margin-right:14px}
.mission-card .figures{font-size:11px;line-height:24px;color:#222;margin-right:10px}
.mission-card .plus{width:22px;height:22px;border-radius:50%;background:var(--green);color:#fff;font-weight:700;font-size:18px;display:flex;align-items:center;justify-content:center;margin-left:12px}
.swipe-hint{position:absolute;left:810px;top:470px;font-size:15px;color:#333;display:flex;gap:28px}
.swipe-hint .dots{color:#aaa;letter-spacing:2px}

.activity-card{position:absolute;width:398px;background:#fff;padding:14px 16px 0 20px;font-size:14px;color:#222}
.activity-card .row{display:flex;justify-content:space-between;align-items:center}
.activity-card .who{display:flex;align-items:center;gap:12px;font-weight:500}
.activity-card .who::before{content:"";width:11px;height:11px;border-radius:50%;background:var(--dot-blue)}
.activity-card time{font-size:11px;color:#555}
.activity-card strong{display:block;margin:4px 0 0 24px}
.activity-card .sub{font-size:12px;color:#666;margin:6px 0 0 24px}

/* team */
.lead-portrait{position:absolute;left:345px;top:67px;width:230px;height:229px;background:linear-gradient(160deg,#6b5140 0%,#b98f78 45%,#d7b6a0 70%,#8a8f96 100%)}
.team-strip{position:absolute;left:190px;top:307px;display:flex;align-items:center;gap:12px}
.team-strip .chev{color:#666;font-size:30px;font-weight:300;width:26px;text-align:center}
.thumb{width:80px;height:80px;border:2px solid #6aa8d8}
.story-dots{position:absolute;left:170px;top:527px}
.story-dots span{display:block;width:14px;height:14px;border-radius:50%;border:2px solid #777;margin-bottom:14px}
.story-dots .on{background:#8c8c93;border-color:#8c8c93}

/* footer */
.site-footer{position:absolute;left:0;top:2910px;width:1200px;height:90px;background:var(--footer);display:flex;justify-content:center;align-items:center;gap:38px;font-family:"Lato",Arial,sans-serif;font-size:20px;color:#fff}
</style>
</head>
<body>

<header class="site-header">
  <div class="menu-toggle">
    <svg width="36" height="28" viewBox="0 0 36 28"><rect y="1" width="36" height="4" fill="#fff"/><rect y="12" width="36" height="4" fill="#fff"/><rect y="23" width="36" height="4" fill="#fff"/></svg>
    SEE THE MISSIONS
  </div>
  <div class="brand">HOPEWINGSRALLY</div>
  <nav class="account-links"><span>LOG IN</span><span>SIGN UP</span></nav>
</header>

<section class="hero" role="img" aria-label="Black and white photograph of two smiling young girls, the smaller one eating an orange treat">
  <p class="hero-quote">
    " She has a Name. He has dreams.<br>
    She hopes she would have a future.<br>
    He is like you."<br>
    <span class="lead">" <span class="amount">1 USD</span> a month will help her and him".</span>
  </p>
</section>
<div class="hero-band"></div>

<!-- about -->
<section class="section about">
  <h2 class="section-title" style="top:18px">ABOUT</h2>

  <h3 class="mission-title" style="left:195px;top:72px">Mission: Orphan Maria, 11y</h3>
  <div class="tabs" style="left:263px;top:110px;width:457px"><span class="active">Story</span><span>Updates</span><span>Comments</span></div>

  <div class="timeline">
    <div class="rail"></div>
    <div class="knob" style="top:0"></div>
    <div class="knob now" style="top:402px;top:206px"></div>
    <div class="knob" style="top:424px"></div>
  </div>

  <div class="story abs" style="left:195px;top:180px;width:510px">
    <p>Lorem ipsum dolor sit amet, sapien etiam, nunc amet dolor ac odio mauris justo. Luctus arcu, urna praesent at id quisque ac. Arcu es massa vestibulum malesuada, integer vivamus elit eu mauris eus, cum eros quis aliquam wisi. Nulla wisi laoreet suspendisse integer vivamus elit eu mauris hendrerit facilisi, mi mattis pariatur aliquam pharetra eget.</p>
    <p>Lorem ipsum dolor sit amet, sapien etiam, nunc amet dolor ac odio mauris justo. Luctus arcu, urna praesent at id quisque ac. Arcu es massa vestibulum malesuada, integer vivamus elit eu mauris eus, cum eros quis aliquam wisi. Nulla wisi laoreet suspendisse integer vivamus elit eu mauris hendrerit facilisi, mi mattis pariatur aliquam pharetra eget.</p>
    <div class="story-still" role="img" aria-label="Photo of a smiling child with a caption overlay">
      <span class="caption">It's simply magical<br><em>when someone smiles because of you</em></span>
    </div>
    <p>Lorem ipsum dolor sit amet, sapien etiam, nunc amet dolor ac odio mauris justo. Luctus arcu, urna praesent at id quisque ac. Arcu es massa vestibulum malesuada, integer vivamus elit eu mauris eus, cum eros quis aliquam wisi. Nulla wisi laoreet suspendisse integer vivamus elit eu mauris hendrerit facilisi, mi mattis pariatur aliquam pharetra eget.</p>
    <p>Lorem ipsum dolor sit amet, sapien etiam, nunc amet dolor ac odio mauris justo. Luctus arcu, urna praesent at id quisque ac. Arcu es massa vestibulum malesuada, integer vivamus elit eu mauris eus, cum eros quis aliquam wisi. Nulla wisi laoreet suspendisse integer vivamus elit eu mauris hendrerit facilisi, mi mattis pariatur aliquam pharetra eget.</p>
  </div>

  <aside class="fund-panel" style="left:752px;top:72px">
    <h3>Name: Maria, 11y</h3>
    <div class="place"><svg width="14" height="20" viewBox="0 0 14 20"><path d="M7 0C3 0 0 3 0 7c0 5 7 13 7 13s7-8 7-13c0-4-3-7-7-7z" fill="#8c8c93"/><circle cx="7" cy="7" r="2.6" fill="#dcdbe8"/></svg>Kalkutta</div>
    <div class="org">Organization: Jacob</div>
    <div class="support-row"><span class="label">Support</span><span class="mini-avatar"></span><span class="mini-avatar"></span><span class="mini-avatar"></span><span class="mini-avatar"></span><span class="mini-avatar"></span><svg width="22" height="20" viewBox="0 0 22 20" style="margin-left:8px"><path d="M8 3l7 7-7 7" fill="none" stroke="#888" stroke-width="2"/></svg></div>
    <div class="my-support">My support is now: $5 / month <span class="close-dot">×</span></div>
    <div class="fund-stats">
      <svg width="96" height="96" viewBox="0 0 96 96"><rect width="96" height="96" fill="#d3d3da"/><circle cx="48" cy="48" r="36" fill="#fff" stroke="#a9a9b0" stroke-width="9"/><circle cx="48" cy="48" r="36" fill="none" stroke="var(--teal)" stroke-width="9" stroke-dasharray="102 226" transform="rotate(-90 48 48)"/><text x="48" y="55" text-anchor="middle" font-family="Roboto,Arial,sans-serif" font-size="20" fill="#777">45%</text></svg>
      <div><div class="given">$15 given</div><small>of total $35 needed</small><div class="need"><svg width="20" height="18" viewBox="0 0 20 18"><rect x="1" y="2" width="18" height="15" fill="none" stroke="#777" stroke-width="1.6"/><path d="M1 6h18M5 9h2M9 9h2M13 9h2M5 13h2M9 13h2M13 13h2" stroke="#777" stroke-width="1.6"/></svg>per month need</div></div>
    </div>
    <div class="participate">Participate</div>
    <ul class="options">
      <li><span class="swatch"></span><span class="label">I am in, $1 / month</span><svg width="24" height="20" viewBox="0 0 24 20"><path d="M1 2h4l3 11h12l2-8H7" fill="none" stroke="#999" stroke-width="1.5"/><circle cx="10" cy="17" r="1.6" fill="#999"/><circle cx="18" cy="17" r="1.6" fill="#999"/></svg></li>
      <li><span class="swatch"></span><span class="label">Increased, $5 / month</span><svg width="24" height="20" viewBox="0 0 24 20"><path d="M1 2h4l3 11h12l2-8H7" fill="none" stroke="#999" stroke-width="1.5"/><circle cx="10" cy="17" r="1.6" fill="#999"/><circle cx="18" cy="17" r="1.6" fill="#999"/></svg></li>
      <li><span class="swatch"></span><span class="label">Decent help, $10 / month</span><svg width="24" height="20" viewBox="0 0 24 20"><path d="M1 2h4l3 11h12l2-8H7" fill="none" stroke="#999" stroke-width="1.5"/><circle cx="10" cy="17" r="1.6" fill="#999"/><circle cx="18" cy="17" r="1.6" fill="#999"/></svg></li>
      <li><span class="swatch"></span><span class="label">Whole kid, $35 / month</span><svg width="24" height="20" viewBox="0 0 24 20"><path d="M1 2h4l3 11h12l2-8H7" fill="none" stroke="#999" stroke-width="1.5"/><circle cx="10" cy="17" r="1.6" fill="#999"/><circle cx="18" cy="17" r="1.6" fill="#999"/></svg></li>
      <li><span class="swatch"></span><span class="label">My amount</span><span class="amount-field">Enter amount</span><svg width="24" height="20" viewBox="0 0 24 20"><path d="M1 2h4l3 11h12l2-8H7" fill="none" stroke="#999" stroke-width="1.5"/><circle cx="10" cy="17" r="1.6" fill="#999"/><circle cx="18" cy="17" r="1.6" fill="#999"/></svg></li>
    </ul>
  </aside>
</section>

<!-- activities -->
<section class="section activities">
  <h2 class="section-title soft" style="top:16px">ACTIVITIES</h2>
  <div class="profile-photo" role="img" aria-label="Default profile silhouette"></div>
  <div class="profile-meta">Name: MATTHEW MATT<br>Username: matt28</div>
  <div class="following">
    <h4>FOLLOWING</h4>
    <ul>
      <li><span class="mini-avatar"></span>Maria,...</li>
      <li><span class="mini-avatar"></span>Maria,...</li>
      <li><span class="mini-avatar"></span>Maria,...</li>
    </ul>
  </div>

  <div class="list-head" style="left:176px;top:224px">MY MISSIONS <svg width="16" height="10" viewBox="0 0 16 10"><path d="M2 2l6 6 6-6" fill="none" stroke="#888" stroke-width="1.6"/></svg></div>

  <div class="mission-card" style="left:176px;top:254px"><span class="avatar"></span><span class="who">Maria, 11y<br>Orphan, Jacob</span><span class="dot"></span><span class="figures">$15 raised<br>$20 to go<br>5 angels in</span><svg width="58" height="58" viewBox="0 0 58 58"><rect width="58" height="58" fill="#e2e2e8"/><circle cx="29" cy="29" r="21" fill="#fff" stroke="#b5b5bc" stroke-width="5"/><circle cx="29" cy="29" r="21" fill="none" stroke="var(--teal)" stroke-width="5" stroke-dasharray="59 132" transform="rotate(-90 29 29)"/><text x="29" y="33" text-anchor="middle" font-size="11" fill="#888" font-family="Roboto,Arial,sans-serif">45°</text></svg><span class="plus">+</span></div>
  <div class="mission-card" style="left:176px;top:335px"><span class="avatar"></span><span class="who">Matthew, 11y<br>Orphan, Jacob</span><span class="dot"></span><span class="figures">$15 raised<br>$20 to go<br>5 angels in</span><svg width="58" height="58" viewBox="0 0 58 58"><rect width="58" height="58" fill="#e2e2e8"/><circle cx="29" cy="29" r="21" fill="#fff" stroke="#b5b5bc" stroke-width="5"/><circle cx="29" cy="29" r="21" fill="none" stroke="var(--teal)" stroke-width="5" stroke-dasharray="59 132" transform="rotate(-90 29 29)"/><text x="29" y="33" text-anchor="middle" font-size="11" fill="#888" font-family="Roboto,Arial,sans-serif">45°</text></svg><span class="plus">+</span></div>
  <div class="mission-card" style="left:176px;top:416px"><span class="avatar"></span><span class="who">Maria, 11y<br>Orphan, Jacob</span><span class="dot"></span><span class="figures">$15 raised<br>$20 to go<br>5 angels in</span><svg width="58" height="58" viewBox="0 0 58 58"><rect width="58" height="58" fill="#e2e2e8"/><circle cx="29" cy="29" r="21" fill="#fff" stroke="#b5b5bc" stroke-width="5"/><circle cx="29" cy="29" r="21" fill="none" stroke="var(--teal)" stroke-width="5" stroke-dasharray="59 132" transform="rotate(-90 29 29)"/><text x="29" y="33" text-anchor="middle" font-size="11" fill="#888" font-family="Roboto,Arial,sans-serif">45°</text></svg><span class="plus">+</span></div>

  <div class="mission-card" style="left:618px;top:254px"><span class="avatar"></span><span class="who">Maria, 11y<br>Orphan, Jacob</span><svg width="58" height="58" viewBox="0 0 58 58"><rect width="58" height="58" fill="#e2e2e8"/><circle cx="29" cy="29" r="21" fill="#fff" stroke="#b5b5bc" stroke-width="5"/><circle cx="29" cy="29" r="21" fill="none" stroke="var(--teal)" stroke-width="5" stroke-dasharray="59 132" transform="rotate(-90 29 29)"/><text x="29" y="33" text-anchor="middle" font-size="11" fill="#888" font-family="Roboto,Arial,sans-serif">45°</text></svg><span class="plus">+</span></div>
  <div class="mission-card" style="left:618px;top:335px"><span class="avatar"></span><span class="who">Matthew, 11y<br>Orphan, Jacob</span><span class="figures">$15 raised<br>$20 to go<br>5 angels in</span><svg width="58" height="58" viewBox="0 0 58 58"><rect width="58" height="58" fill="#e2e2e8"/><circle cx="29" cy="29" r="21" fill="#fff" stroke="#b5b5bc" stroke-width="5"/><circle cx="29" cy="29" r="21" fill="none" stroke="var(--teal)" stroke-width="5" stroke-dasharray="59 132" transform="rotate(-90 29 29)"/><text x="29" y="33" text-anchor="middle" font-size="11" fill="#888" font-family="Roboto,Arial,sans-serif">45°</text></svg><span class="plus">+</span></div>

  <div class="swipe-hint"><span class="dots">• • •</span><span>Swipe to</span><span>see more?</span></div>

  <div class="list-head" style="left:176px;top:510px">ACTIVITIES <svg width="12" height="16" viewBox="0 0 12 16"><path d="M3 2l6 6-6 6" fill="none" stroke="#888" stroke-width="1.6"/></svg></div>

  <article class="activity-card" style="left:172px;top:537px;height:125px">
    <div class="row"><span class="who">Maria</span><time>10:51 AM ›</time></div>
    <strong>Report</strong>
    <div class="sub">Half year report.....</div>
  </article>
  <article class="activity-card" style="left:582px;top:537px;height:125px">
    <div class="row"><span class="who">Maria</span><time>10:51 AM ›</time></div>
    <strong>Got a new angel</strong>
    <div style="display:flex;align-items:center;gap:40px;margin:6px 0 0 24px"><span class="mini-avatar" style="width:46px;height:46px;margin:0"></span><span class="sub" style="margin:0">Anonymous</span></div>
  </article>
  <article class="activity-card" style="left:172px;top:672px;height:35px;padding-top:10px">
    <div class="row"><span class="who">Imma Mustard</span><time>10:51 AM ›</time></div>
  </article>
  <article class="activity-card" style="left:582px;top:672px;height:35px;padding-top:10px">
    <div class="row"><span class="who">Matthew</span><time>10:51 AM ›</time></div>
  </article>
</section>

<!-- team -->
<section class="section team">
  <h2 class="section-title" style="top:10px">TEAM</h2>
  <div class="lead-portrait" role="img" aria-label="Portrait photo of the featured team member"></div>
  <div class="team-strip">
    <span class="chev">‹</span>
    <span class="thumb" role="img" aria-label="Team member photo" style="background:linear-gradient(160deg,#e2b48a,#c78a5e)"></span>
    <span class="thumb" role="img" aria-label="Team member photo" style="background:linear-gradient(160deg,#9c7a64,#d8b49a)"></span>
    <span class="thumb" role="img" aria-label="Team member photo" style="background:linear-gradient(160deg,#4fae5c,#8fd08a)"></span>
    <span class="thumb" role="img" aria-label="Team member photo" style="background:linear-gradient(160deg,#c9c2b8,#8e6e5c)"></span>
    <span class="thumb" role="img" aria-label="Team member photo" style="background:linear-gradient(160deg,#b08a6a,#e0c09a)"></span>
    <span class="chev">›</span>
  </div>

  <h3 class="mission-title" style="left:211px;top:407px">Mission: Orphan Maria, 11y</h3>
  <div class="tabs" style="left:211px;top:450px;width:511px"><span class="active">Story</span><span>Updates</span><span>Comments</span></div>
  <div class="story-dots"><span class="on"></span><span></span><span></span></div>
  <div class="story abs" style="left:211px;top:493px;width:505px">
    <p>Lorem ipsum dolor sit amet, sapien etiam, nunc amet dolor ac odio mauris justo. Luctus arcu, urna praesent at id quisque ac. Arcu es massa vestibulum malesuada, integer vivamus elit eu mauris eus, cum eros quis aliquam wisi. Nulla wisi laoreet suspendisse integer vivamus elit eu mauris hendrerit facilisi, mi mattis pariatur aliquam pharetra eget.</p>
    <p>Lorem ipsum dolor sit amet, sapien etiam, nunc amet dolor ac odio mauris justo. Luctus arcu, urna praesent at id quisque ac. Arcu es massa vestibulum malesuada, integer vivamus elit eu mauris eus, cum eros quis aliquam wisi. Nulla wisi laoreet suspendisse integer vivamus elit</p>
  </div>

  <aside class="fund-panel" style="left:748px;top:72px;width:292px">
    <h3>Name: Maria, 11y</h3>
    <div class="place"><svg width="14" height="20" viewBox="0 0 14 20"><path d="M7 0C3 0 0 3 0 7c0 5 7 13 7 13s7-8 7-13c0-4-3-7-7-7z" fill="#8c8c93"/><circle cx="7" cy="7" r="2.6" fill="#cfcedd"/></svg>Kalkutta</div>
    <div class="org">Organization: Jacob</div>
    <div class="support-row"><span class="label">Support</span><span class="mini-avatar"></span><span class="mini-avatar"></span><span class="mini-avatar"></span><span class="mini-avatar"></span><span class="mini-avatar"></span><svg width="22" height="20" viewBox="0 0 22 20" style="margin-left:8px"><path d="M8 3l7 7-7 7" fill="none" stroke="#888" stroke-width="2"/></svg></div>
    <div class="my-support" style="padding-right:30px">My support is now: $5 / month <span class="close-dot">×</span></div>
    <div class="fund-stats">
      <svg width="96" height="96" viewBox="0 0 96 96"><rect width="96" height="96" fill="#c4c3d1"/><circle cx="48" cy="48" r="36" fill="#fff" stroke="#a9a9b0" stroke-width="9"/><circle cx="48" cy="48" r="36" fill="none" stroke="var(--teal)" stroke-width="9" stroke-dasharray="102 226" transform="rotate(-90 48 48)"/><text x="48" y="55" text-anchor="middle" font-family="Roboto,Arial,sans-serif" font-size="20" fill="#777">45%</text></svg>
      <div><div class="given">$15 given</div><small>of total $35 needed</small><div class="need"><svg width="20" height="18" viewBox="0 0 20 18"><rect x="1" y="2" width="18" height="15" fill="none" stroke="#777" stroke-width="1.6"/><path d="M1 6h18M5 9h2M9 9h2M13 9h2M5 13h2M9 13h2M13 13h2" stroke="#777" stroke-width="1.6"/></svg>per month need</div></div>
    </div>
    <div class="participate">Participate</div>
    <ul class="options">
      <li><span class="swatch"></span><span class="label">I am in, $1</span></li>
      <li><span class="swatch"></span><span class="label">Increased, $5 / month</span></li>
      <li><span class="swatch"></span><span class="label">Decent help, $10 / month</span></li>
      <li><span class="swatch"></span><span class="label">Whole kid, $35 / month</span></li>
      <li><span class="swatch"></span><span class="label">My amount</span><span class="amount-field" style="margin-right:0">Enter amount</span></li>
    </ul>
  </aside>
</section>

<footer class="site-footer">
  <span>Contact</span><span>Download</span><span>Press</span><span>Email</span><span>Support</span><span>Privacy Policy</span>
</footer>

</body>
</html>
```